Home Remodeling company needs a business card design

we need a business card design for home remodeling company in hamilton county, indiana USA. we offers a wide range of construction services including whole house renovations, Design and Build Basements and Kitchen and Bathroom Remodeling . we would like to see designs for both site of business card that use the same color of the company logo and also including all information below :
1- Karim Feltous CEO / General Contractor
2- all company contacts Telephone numbers ( 1-888-DULOM-47 ) ( 317-555-0193) email address ( info@dulomhome.com) website ( www.dulomhome.com ) and social media logos (Facebook- twitter- google plus )
3- company logo
4- licensed . insured . bonded

```html
<!DOCTYPE html>
<html lang="en">
<head>
<meta charset="utf-8">
<title>Dulom Home Remodeling – Business Card</title>
<link rel="stylesheet" href="https://fonts.googleapis.com/css2?family=Cabin:wght@400;500;700&display=swap">
<style>
  :root {
    --backdrop: #858585;
    --card-white: #ecebec;
    --ink: #2f2f31;
    --ink-soft: #3a3a3c;
    --band: #333335;
    --band-text: #f1f1f1;
    --brand-red: #a9282f;
    --on-red: #eeeeee;
    --on-red-line: rgba(238, 238, 238, 0.55);
  }
  * { margin: 0; padding: 0; box-sizing: border-box; }
  html, body {
    width: 1105px;
    height: 1200px;
    overflow: hidden;
    background: var(--backdrop);
    font-family: "Cabin", "Gill Sans", sans-serif;
  }
  .sheet {
    position: relative;
    width: 1105px;
    height: 1200px;
  }
  .card {
    position: absolute;
    left: 182px;
    width: 747px;
    height: 427px;
  }
  /* Front */
  .card-front {
    top: 119px;
    background: var(--card-white);
  }
  .name-band {
    position: absolute;
    left: 0;
    top: 50px;
    width: 403px;
    height: 59px;
    background: var(--band);
    color: var(--band-text);
    padding: 5px 0 0 50px;
  }
  .person-name {
    font-size: 23px;
    font-weight: 500;
    letter-spacing: 0.3px;
    line-height: 1.1;
  }
  .person-role {
    font-size: 18.5px;
    font-weight: 400;
    line-height: 1.2;
  }
  .brand-lockup {
    position: absolute;
    left: 410px;
    top: 44px;
    display: flex;
    align-items: center;
    gap: 12px;
  }
  .brand-square {
    width: 9px;
    height: 60px;
    background: var(--brand-red);
  }
  .brand-name {
    font-size: 56px;
    font-weight: 700;
    color: var(--ink);
    letter-spacing: 1px;
    line-height: 1;
  }
  .contact-list {
    position: absolute;
    left: 52px;
    top: 269px;
    list-style: none;
    color: var(--ink-soft);
    font-size: 19.5px;
  }
  .contact-item {
    display: flex;
    align-items: center;
    height: 29px;
  }
  .contact-icon {
    width: 18px;
    height: 18px;
    margin-right: 11px;
    fill: var(--ink);
    flex: none;
  }
  /* Back */
  .card-back {
    top: 637px;
    background: var(--brand-red);
    color: var(--on-red);
  }
  .back-brand {
    position: absolute;
    left: 0;
    right: 0;
    top: 152px;
    text-align: center;
    font-size: 64px;
    font-weight: 700;
    letter-spacing: 3px;
    line-height: 1;
  }
  .credentials {
    position: absolute;
    left: 0;
    right: 0;
    top: 320px;
    text-align: center;
    font-size: 22.5px;
    font-weight: 400;
    letter-spacing: 0.3px;
  }
  .social-row {
    position: absolute;
    left: 0;
    right: 0;
    top: 361px;
    display: flex;
    justify-content: center;
    align-items: center;
    gap: 4px;
  }
  .social-rule {
    width: 66px;
    height: 1px;
    background: var(--on-red-line);
  }
  .social-dot {
    width: 26px;
    height: 26px;
    border-radius: 50%;
    background: var(--on-red);
  }
</style>
</head>
<body>
<main class="sheet">
  <section class="card card-front" aria-label="Business card front">
    <div class="name-band">
      <p class="person-name">Karim Feltous</p>
      <p class="person-role">CEO / General Contractor</p>
    </div>
    <div class="brand-lockup">
      <span class="brand-square"></span>
      <span class="brand-name">DULOM</span>
    </div>
    <ul class="contact-list">
      <li class="contact-item">
        <svg class="contact-icon" viewBox="0 0 24 24" aria-hidden="true"><path d="M6.6 10.8a15.1 15.1 0 0 0 6.6 6.6l2.2-2.2a1 1 0 0 1 1-.25 11.4 11.4 0 0 0 3.6.57 1 1 0 0 1 1 1V20a1 1 0 0 1-1 1A17 17 0 0 1 3 4a1 1 0 0 1 1-1h3.5a1 1 0 0 1 1 1c0 1.25.2 2.45.57 3.57a1 1 0 0 1-.25 1z"/></svg>
        <span>1-888-DULOM-47</span>
      </li>
      <li class="contact-item">
        <svg class="contact-icon" viewBox="0 0 24 24" aria-hidden="true"><path d="M7 1h10a2 2 0 0 1 2 2v18a2 2 0 0 1-2 2H7a2 2 0 0 1-2-2V3a2 2 0 0 1 2-2zm0 3v15h10V4zm5 16.2a1 1 0 1 0 0 1.6 1 1 0 0 0 0-1.6z"/></svg>
        <span>317-555-0193</span>
      </li>
      <li class="contact-item">
        <svg class="contact-icon" viewBox="0 0 24 24" aria-hidden="true"><path d="M2 5h20v14H2zm2 2v.4l8 5.2 8-5.2V7zm0 2.8V17h16V9.8l-8 5.2z"/></svg>
        <span>info@dulomhome.com</span>
      </li>
      <li class="contact-item">
        <svg class="contact-icon" viewBox="0 0 24 24" aria-hidden="true"><path d="M12 2a10 10 0 1 0 0 20 10 10 0 0 0 0-20zm-1 17.9A8 8 0 0 1 4.2 10L9 14.8v1a2 2 0 0 0 2 2zm6.9-2.5A2 2 0 0 0 16 16h-1v-3a1 1 0 0 0-1-1H8v-2h2a1 1 0 0 0 1-1V7h2a2 2 0 0 0 2-2v-.4a8 8 0 0 1 2.9 12.8z"/></svg>
        <span>www.dulomhome.com</span>
      </li>
    </ul>
  </section>

  <section class="card card-back" aria-label="Business card back">
    <p class="back-brand">DULOM</p>
    <p class="credentials">LICENSED | INSURED | BONDED</p>
    <div class="social-row" aria-label="Social media links">
      <span class="social-rule"></span>
      <span class="social-dot"></span>
      <span class="social-dot"></span>
      <span class="social-dot"></span>
      <span class="social-rule"></span>
    </div>
  </section>
</main>
</body>
</html>
```